Business Card for Coastal Tundrabridge Advisory

We need a business card for Coastal Tundrabridge Advisory. The company website address is provided below. The company logo is attached. We provide specialized permafrost services to the mining, transportation, and oil & gas industries. The card should be prepared for:
Matthias Korhonen, PhD.
Coastal Tundrabridge Advisory
PO Box 418259
Quillwater, Alaska 99642
Direct: +1-907-555-0143
Email: mkorhonen@tundrabridgeadvisory.example
Website: www.coastaltundrabridgeadvisory.example

```html
<!DOCTYPE html>
<html lang="en">
<head>
<meta charset="utf-8">
<title>Coastal Tundrabridge Advisory – Business Card</title>
<link rel="stylesheet" href="https://fonts.googleapis.com/css2?family=Montserrat:wght@400;600;700&display=swap">
<style>
  :root {
    --backdrop: #e7e4df;
    --card-white: #ffffff;
    --card-dark: #222222;
    --card-dark-edge: #2b2b2b;
    --ink: #121a22;
    --band-dark: #333234;
    --band-grey: #6f6f6f;
    --text-light: #ffffff;
  }
  * { margin: 0; padding: 0; box-sizing: border-box; }
  html, body {
    width: 900px; height: 1200px; overflow: hidden;
    background: var(--backdrop);
    font-family: "Montserrat", Arial, sans-serif;
  }
  .canvas { position: relative; width: 900px; height: 1200px; }

  .card {
    position: absolute; left: 80px; width: 742px; height: 440px;
    border-radius: 32px; overflow: hidden;
  }
  .card-front { top: 132px; background: var(--card-white); }
  .card-back { top: 638px; height: 442px; background: var(--card-dark); }

  .wordmark {
    position: absolute; font-weight: 700; letter-spacing: 2px;
    text-transform: uppercase; white-space: nowrap;
  }
  .card-front .wordmark {
    left: 55px; top: 64px; font-size: 24px; color: var(--ink);
  }
  .card-back .wordmark {
    left: 0; right: 0; top: 186px; text-align: center;
    font-size: 28px; color: var(--text-light);
  }
  .back-footer {
    position: absolute; left: 0; right: 0; bottom: 0; height: 18px;
    background: var(--card-dark-edge);
  }

  .holder { position: absolute; left: 38px; top: 236px; color: var(--ink); }
  .holder-name { font-size: 25px; font-weight: 700; line-height: 1.2; }
  .holder-title { font-size: 15px; font-weight: 400; margin-top: 2px; }

  .bands { position: absolute; left: 0; top: 301px; width: 742px; height: 103px; }

  .contact-list {
    position: absolute; left: 45px; top: 320px; list-style: none;
    color: var(--text-light); font-size: 15.5px; line-height: 22.5px;
  }
  .contact-list li { display: flex; align-items: center; gap: 12px; }
  .contact-list svg { width: 14px; height: 14px; fill: var(--text-light); flex: none; }

  .address {
    position: absolute; left: 518px; top: 350px;
    color: var(--text-light); font-size: 15.5px; line-height: 20px;
  }
</style>
</head>
<body>
<main class="canvas">

  <section class="card card-front" aria-label="Card front">
    <div class="wordmark">Coastal Tundrabridge Advisory</div>

    <div class="holder">
      <div class="holder-name">Matthias Korhonen, PhD.</div>
      <div class="holder-title">CEO &amp; Founder</div>
    </div>

    <svg class="bands" viewBox="0 0 742 103" aria-hidden="true">
      <polygon points="0,0 518,0 460,103 0,103" fill="var(--band-dark)"/>
      <polygon points="525,0 742,0 742,103 468,103" fill="var(--band-grey)"/>
    </svg>

    <ul class="contact-list">
      <li>
        <svg viewBox="0 0 16 16"><path d="M2 6c0-2 3-3 6-3s6 1 6 3v1h-3V6H5v1H2zM4 8h8l1 5H3z"/></svg>
        +1-907-555-0143
      </li>
      <li>
        <svg viewBox="0 0 16 16"><path d="M1 3h14v10H1zM2 4l6 5 6-5v-.1H2z" fill-rule="evenodd"/></svg>
        mkorhonen@tundrabridgeadvisory.example
      </li>
      <li>
        <svg viewBox="0 0 16 16"><circle cx="8" cy="8" r="7"/><path d="M5 5h3v3H5zM9 9h3v2H9z" fill="var(--band-dark)"/></svg>
        www.coastaltundrabridgeadvisory.example
      </li>
    </ul>

    <div class="address">
      PO Box 418259<br>
      Quillwater, Alaska 99642
    </div>
  </section>

  <section class="card card-back" aria-label="Card back">
    <div class="wordmark">Coastal Tundrabridge Advisory</div>
    <div class="back-footer"></div>
  </section>

</main>
</body>
</html>
```